Orthobiologic, StemCell, Bone Marrow Aspirate Device Distributor

We need a wordpress fully functioning website design for an innovative ortho-biologic, Bone Marrow Aspirate Device that extracts stem cells for orthopedic regenerative medical professionals. We also offer state of the art training in there office setting with licensed medical staff, a full service support team, and software for tracking patient outcome over time. We are an innovative company that prides itself on gold standard support. We will have other offerings on our website and would like a spot for "future" products. We would like to see designs that look professional, medical, and convey support, security, science, and innovation. We prefer shades of blue and red/orange. I particularly like the following websites that also sell the same device in order of preference:regenacelltherapy.comhttps://aspire-medical.eu/marrow-cellution/https://www.matrixbiosurgical.com/#emerging-solutions-in-healthcareElite2elite.comI have attached a few pictures of the device for reference

Target Market(s)

Orthopedics, Regenerative medicine doctors, Industry representatives, Hospitals

Industry/Entity Type

Medical Equipment

Coding

Coded - Design and coding required

Colors
3176b5
33a6d7
f37022
ec1f27

Requirements
Must have
• It must be able to have videos which I can supply, email, online ordering, and sfax. I have a domain name Coralweavesolutions.com . It must have a FAQ section which you can obtain some information from https://www.tolvenclinical.com/solutions#resources
• The device is manufactured by Dulmor and this is the link to the product page http://www.dulmor.com/quintadraw
• I am currently working on a custom logo and should be able to supply that in short order. I prefer shades of blue and red.
Nice to have
• I would love to have a graphic video as seen here: please see quinta draw vs bone marrow aspirate concentrate.
• https://www.tolvenclinical.com/solutions#competition
• I would pay considerably more to have something similar if it is at all possible
Should not have
• Nothing specific

```html
<!DOCTYPE html>
<html lang="en">
<head>
<meta charset="utf-8">
<title>Coral Weave Solutions</title>
<link href="https://fonts.googleapis.com/css2?family=Lato:wght@300;400;700;900&display=swap" rel="stylesheet">
<style>
:root{
  --brand:#2a6bb8;
  --brand-dark:#1f5aa0;
  --sky:#dce8f0;
  --ink:#2b2b2b;
  --muted:#6d6d6d;
  --orange:#f37022;
  --red:#ec1f27;
  --footer:#f1f1f1;
  --white:#ffffff;
}
*{box-sizing:border-box;margin:0;padding:0}
html,body{width:1200px;height:4505px;overflow:hidden}
body{font-family:'Lato',sans-serif;color:var(--ink);background:var(--white);position:relative}
section,header,footer{position:relative;width:1200px;overflow:hidden}
.abs{position:absolute}
a{color:inherit;text-decoration:none}

/* header */
.site-header{height:95px;background:var(--white)}
.logo{left:149px;top:20px;color:var(--brand);font-weight:900;line-height:1}
.logo .l1{font-size:26px;letter-spacing:0.5px;display:block}
.logo .l2{font-size:21px;letter-spacing:5px;font-weight:400;display:block;margin-top:4px}
.main-nav{right:133px;top:38px;display:flex;gap:37px;font-size:18px;color:#222}

/* hero */
.hero{height:570px;background:radial-gradient(ellipse at 50% 40%,#3d6de0 0%,#1d3c9a 30%,#0c1a4a 65%,#060c22 100%)}
.hero-title{width:100%;text-align:center;top:215px;color:var(--white);font-size:48px;font-weight:700}
.hero-sub{width:100%;text-align:center;top:280px;color:#e6ecff;font-size:24px;font-weight:400}
.arrow-btn{top:230px;width:58px;height:58px;border-radius:50%;background:rgba(220,220,220,.55);display:flex;align-items:center;justify-content:center}

/* about */
.about{height:378px;text-align:center}
.about h2{position:absolute;top:85px;width:100%;font-weight:400;font-size:34px;color:var(--brand)}
.about p{position:absolute;top:148px;left:250px;width:700px;font-size:16.5px;line-height:27px;color:#555}
.about svg{position:absolute;left:581px;top:275px}

/* advantage */
.advantage{height:456px;background:var(--sky)}
.advantage-photo{left:0;top:0;width:595px;height:456px;background:radial-gradient(ellipse at 55% 50%,#1d5fb8 0%,#6a9ed6 40%,#c9dced 75%,var(--sky) 100%)}
.advantage h2{left:607px;top:84px;font-size:30px;font-weight:400;color:#333}
.advantage .txt{left:612px;top:143px;width:440px;font-size:13.5px;line-height:21.5px;color:#555}
.advantage .txt p+p{margin-top:21px}
.btn-outline{display:flex;align-items:center;justify-content:center;border:2px solid var(--brand);border-radius:26px;color:var(--brand);font-size:15px;font-weight:700}
.advantage .btn-outline{left:613px;top:327px;width:165px;height:50px}

/* mission / why */
.mission{height:541px}
.mission h2,.why h2{font-size:30px;font-weight:400;color:var(--brand)}
.mission h2{left:167px;top:88px}
.mission .txt{left:171px;top:150px;width:400px;font-size:13.5px;line-height:21.5px;color:#555}
.mission .txt p+p{margin-top:21px}
.why{left:607px;top:88px;width:460px}
.why-item{display:flex;gap:24px;position:absolute;left:4px}
.why-item h3{font-size:19px;font-weight:700;color:#222;margin-top:2px}
.why-item p{font-size:13.5px;line-height:21.5px;color:#555;margin-top:8px;width:360px}

/* band */
.band{height:524px;background:linear-gradient(90deg,#1a1a1a 0%,#5a5a5a 30%,#2e2e2e 55%,#6a6a6a 80%,#222 100%)}
.band-box{left:264px;top:76px;width:666px;height:364px;background:rgba(33,110,190,.92);text-align:center;color:var(--white)}
.band-box h2{margin-top:65px;font-size:34px;font-weight:400}
.band-box p{margin:18px auto 0;width:540px;font-size:17px;line-height:27px}
.band-box .btn-outline{border-color:var(--white);color:var(--white);width:163px;height:48px;margin:20px auto 0}

/* products */
.products{height:591px}
.products h2{top:73px;width:100%;text-align:center;font-size:32px;font-weight:400;color:#333}
.card{top:149px;width:277px;height:362px;border:2px solid #e2e2e2;text-align:center;background:var(--white)}
.card-img{margin:20px auto 0;width:200px;height:150px;border-radius:4px}
.card h3{margin-top:30px;font-size:18px;font-weight:700;color:#333}
.card p{margin:10px auto 0;width:230px;font-size:13px;line-height:21px;color:#666}
.btn-red{display:flex;align-items:center;justify-content:center;margin:14px auto 0;width:140px;height:42px;border:2px solid var(--red);border-radius:22px;color:var(--red);font-size:13px}

/* faq */
.faq{height:581px;background:linear-gradient(110deg,#f05a1e 0%,#ee3a22 50%,#e8101e 100%);color:var(--white)}
.faq h2{top:42px;width:100%;text-align:center;font-size:34px;font-weight:400}
.faq-item{left:222px;width:766px;border:2px solid rgba(255,255,255,.6);padding:0 22px}
.faq-item h3{font-size:14px;font-weight:700;line-height:22px;width:660px}
.faq-item p{font-size:13.5px;line-height:20px;margin-top:10px;width:700px}
.faq-item .sign{position:absolute;right:22px;font-size:24px;font-weight:400}

/* tiles */
.tiles{height:374px;display:flex}
.tile{position:relative;height:374px;text-align:center;color:var(--white)}
.tile h2{margin-top:145px;font-size:28px;font-weight:400}
.tile .btn-outline{border-color:var(--white);color:var(--white);font-size:12px;font-weight:400;width:140px;height:40px;margin:12px auto 0}

/* footer */
.site-footer{height:326px;background:var(--footer)}
.f-col{top:72px;font-size:13.5px;color:#555}
.f-col h4{font-size:15px;font-weight:900;color:#222;margin-bottom:14px}
.f-col li{list-style:none;line-height:26px}
.contact li{display:flex;gap:12px;margin-bottom:10px;line-height:18px}
.social li{display:flex;align-items:center;gap:12px;margin-bottom:8px}
.dot{width:24px;height:24px;border-radius:50%;background:var(--brand-dark)}
.copyright{height:69px;background:var(--footer);border-top:1px solid #ddd;text-align:center;font-size:13.5px;color:#999;padding-top:24px}
</style>
</head>
<body>

<header class="site-header">
  <a class="logo abs" href="#"><span class="l1">CORAL WEAVE</span><span class="l2">SOLUTIONS</span></a>
  <nav class="main-nav abs">
    <a href="#">ABOUT</a><a href="#">PRODUCTS</a><a href="#">SERVICES</a><a href="#">SOLUTION</a><a href="#">NEWS</a><a href="#">CONTACT</a>
  </nav>
</header>

<section class="hero" role="img" aria-label="Blue x-ray image of a human spine and rib cage with circuit lines">
  <div class="arrow-btn abs" style="left:106px"><svg width="20" height="20" viewBox="0 0 20 20"><path d="M13 3 6 10l7 7" fill="none" stroke="#333" stroke-width="2.5"/></svg></div>
  <div class="arrow-btn abs" style="left:1066px"><svg width="20" height="20" viewBox="0 0 20 20"><path d="M7 3l7 7-7 7" fill="none" stroke="#333" stroke-width="2.5"/></svg></div>
  <h1 class="hero-title abs">INNOVATIVE ORTHO-BIOLOGIC</h1>
  <p class="hero-sub abs">EXTRACTS STEM CELLS FOR ORTHOPEDIC REGENERATIVE</p>
</section>

<section class="about">
  <h2>ABOUT CORAL WEAVE SOLUTIONS</h2>
  <p>Duis non nunc Nulla rhoncus dictum metus Curabitur tristique mi condimentum orci Phasellus pellentesque aliquam enim Proin dui lectus cursus eu mattis laoreet viverra sit amet quam Curabitur vel dolor ultrices ipsum dictum tristique</p>
  <svg width="38" height="50" viewBox="0 0 38 50"><path d="M19 2v44M4 31l15 15 15-15" fill="none" stroke="#2a6bb8" stroke-width="2.5"/></svg>
</section>

<section class="advantage">
  <div class="advantage-photo abs" role="img" aria-label="Blue x-ray of a human pelvis and lower spine"></div>
  <h2 class="abs">OUR ADVANTAGE</h2>
  <div class="txt abs">
    <p>Sed porta Suspendisse quam leo molestie sed luctus quis feugiat in pede Fusce tellus Sed metus augue convallis et vehicula ut pulvinar eu ante Integer orci tellus</p>
    <p>Curabitur tristique mi condimentum orci Phasellus pellentesque aliquam enim Proin dui lectus cursus eu mattis laoreet viverra sit amet quam Curabitur</p>
  </div>
  <a class="btn-outline abs" href="#">CLICK HERE</a>
</section>

<section class="mission">
  <h2 class="abs">OUR MISSION</h2>
  <div class="txt abs">
    <p>Sed porta Suspendisse quam leo molestie sed luctus quis feugiat in pede Fusce tellus Sed metus augue convallis et vehicula ut pulvinar eu ante Integer orci tellus sit amet diam Duis non nunc Nulla rhoncus dictum metus</p>
    <p>Curabitur tristique mi condimentum orci Phasellus pellentesque aliquam enim Proin dui lectus cursus eu mattis laoreet viverra sit amet quam Curabitur vel dolor ultrices ipsum dictum tristique Praesent vitae lacus</p>
    <p>Ut velit enim vestibulum non fermentum nec hendrerit quis leo Pellentesque rutrum malesuada neque</p>
  </div>
  <div class="why abs">
    <h2>WHY WE ARE</h2>
    <div class="why-item" style="top:62px">
      <svg width="62" height="70" viewBox="0 0 62 70" fill="none" stroke="#f37022" stroke-width="2"><circle cx="31" cy="28" r="18"/><path d="M24 46v10h14V46M26 60h10M31 4v-2M9 28H5M57 28h-4M15 12l-3-3M47 12l3-3"/><path d="M25 30c0-6 12-6 12 0"/></svg>
      <div><h3>INNOVATIVE</h3><p>Vivamus porttitor purus nisi eleifend libero a tempus libero lectus feugiat felis Morbi diam mauris viverra in</p></div>
    </div>
    <div class="why-item" style="top:182px">
      <svg width="62" height="62" viewBox="0 0 62 62" fill="none" stroke="#f37022" stroke-width="2"><circle cx="31" cy="31" r="27"/><circle cx="31" cy="31" r="19"/><path d="M31 31l9-9M16 34h6M40 34h6M31 16v5"/><circle cx="31" cy="31" r="3"/></svg>
      <div><h3>EFFICIENT</h3><p>Vivamus porttitor purus nisi eleifend libero a tempus libero lectus feugiat felis Morbi diam mauris</p></div>
    </div>
    <div class="why-item" style="top:298px">
      <svg width="62" height="66" viewBox="0 0 62 66" fill="none" stroke="#f37022" stroke-width="2"><circle cx="33" cy="28" r="24"/><circle cx="33" cy="28" r="10"/><path d="M10 38c-4 10 0 20 10 24"/></svg>
      <div><h3>SPECIFIC</h3><p>Vivamus porttitor purus nisi eleifend libero a tempus libero lectus feugiat felis Morbi diam mauris</p></div>
    </div>
  </div>
</section>

<section class="band" role="img" aria-label="Grey x-ray of hip joints and femur bones">
  <div class="band-box abs">
    <h2>WHY WE ARE</h2>
    <p>Duis non nunc Nulla rhoncus dictum metus Curabitur tristique mi condimentum orci Phasellus pellentesque aliquam enim Proin dui lectus cursus eu mattis laoreet viverra sit amet quam Curabitur vel dolor ultrices ipsum dictum tristique a</p>
    <a class="btn-outline" href="#">CLICK HERE</a>
  </div>
</section>

<section class="products">
  <h2 class="abs">OUR PRODUCTS</h2>
  <div class="card abs" style="left:161px">
    <div class="card-img" role="img" aria-label="Bone marrow aspiration needle set with green handle" style="background:linear-gradient(135deg,#f4f4f4,#cfd6d2 45%,#5a8f5e 55%,#eef0ee)"></div>
    <h3>PRODUCT TITLE</h3><p>Sed ut perspiciatis unde omnis iste natus error sit voluptatem</p><a class="btn-red" href="#">CLICK HERE</a>
  </div>
  <div class="card abs" style="left:457px">
    <div class="card-img" role="img" aria-label="Aspiration device with blue handle and threaded tip" style="background:linear-gradient(135deg,#f4f4f4,#c9cbe2 45%,#3330a0 55%,#eeeef4)"></div>
    <h3>PRODUCT TITLE</h3><p>Sed ut perspiciatis unde omnis iste natus error sit voluptatem</p><a class="btn-red" href="#">CLICK HERE</a>
  </div>
  <div class="card abs" style="left:753px">
    <div class="card-img" role="img" aria-label="Stainless steel cannula tip component" style="background:linear-gradient(135deg,#f6f6f6,#b9bcbf 50%,#eaeaea)"></div>
    <h3>PRODUCT TITLE</h3><p>Sed ut perspiciatis unde omnis iste natus error sit voluptatem</p><a class="btn-red" href="#">CLICK HERE</a>
  </div>
</section>

<section class="faq">
  <h2 class="abs">FAQ</h2>
  <div class="faq-item abs" style="top:112px;height:132px;padding-top:15px">
    <h3>DOES A SMALL VOLUME ASPIRATE HAVE MORE CFU-F THAN A LARGER DRAW THAT IS THEN VOLUME REDUCED BY CENTRIFUGATION?</h3>
    <p>Pellentesque faucibus Ut accumsan ultricies elit Maecenas at justo id velit placerat molestie Donec dictum lectus non odio Cras a ante vitae enim iaculis aliquam Mauris nunc quam venenatis nec</p>
    <span class="sign" style="top:12px">–</span>
  </div>
  <div class="faq-item abs" style="top:259px;height:74px;padding-top:14px">
    <h3>WHAT ARE THE LIMITATIONS OF TRADITIONAL NEEDLES AND WHAT IS THE OPTIMAL TECHNIQUE FOR MINIMIZAING PERIPHERAL BLOOD DILUTION?</h3>
    <span class="sign" style="top:20px">+</span>
  </div>
  <div class="faq-item abs" style="top:346px;height:74px;padding-top:14px">
    <h3>DO I NEED TO FILTER SPICULES FROM MARROW AFTER ASPIRATION AND ARE RED CELLS A PROBLEM?</h3>
    <span class="sign" style="top:20px">+</span>
  </div>
  <div class="faq-item abs" style="top:428px;height:74px;padding-top:14px">
    <h3>IS THERE A RELATIONSHIP BETWEEN DIFFERING VOLUMES OF BONE MARROW ASPIRATES AND THEIR CELLULAR COMPOSITION?</h3>
    <span class="sign" style="top:20px">+</span>
  </div>
</section>

<section class="tiles">
  <div class="tile" style="width:397px;background:radial-gradient(ellipse at 50% 50%,#3a5f9a 0%,#152a52 60%,#0b1733 100%)" role="img" aria-label="Dark blue x-ray of a rib cage">
    <h2>DISTRIBUTORS</h2><a class="btn-outline" href="#">CLICK HERE</a>
  </div>
  <div class="tile" style="width:405px;background:linear-gradient(135deg,#2d62c2 0%,#2458b8 50%,#3b6fcc 100%)" role="img" aria-label="Blue-tinted x-ray film held over a bright surface">
    <h2>OUR BLOGS</h2><a class="btn-outline" href="#">CLICK HERE</a>
  </div>
  <div class="tile" style="width:398px;background:radial-gradient(ellipse at 50% 55%,#3f6fc2 0%,#173266 55%,#0a1632 100%)" role="img" aria-label="Blue x-ray of a pelvis">
    <h2>RESOURCES</h2><a class="btn-outline" href="#">CLICK HERE</a>
  </div>
</section>

<footer class="site-footer">
  <div class="f-col abs contact" style="left:169px">
    <h4>CONTACT US</h4>
    <ul>
      <li><svg width="18" height="18" viewBox="0 0 18 18" fill="none" stroke="#333" stroke-width="1.5"><path d="M9 17s-6-6-6-10a6 6 0 0 1 12 0c0 4-6 10-6 10z"/><circle cx="9" cy="7" r="2"/></svg><span>482 Larkmoor Avenue #12<br>Fenwick 70318 TX</span></li>
      <li><svg width="18" height="18" viewBox="0 0 18 18" fill="none" stroke="#333" stroke-width="1.5"><path d="M3 2h4l1 4-2 1.5a9 9 0 0 0 4.5 4.5L12 10l4 1v4a1 1 0 0 1-1 1A14 14 0 0 1 2 3a1 1 0 0 1 1-1z"/></svg><span>555.014.7390</span></li>
      <li><svg width="18" height="18" viewBox="0 0 18 18" fill="none" stroke="#333" stroke-width="1.5"><rect x="2" y="4" width="14" height="10"/><path d="M2 4l7 6 7-6"/></svg><span>info@coralweavesolutions.com</span></li>
    </ul>
  </div>
  <div class="f-col abs" style="left:426px"><h4>COMPANY</h4><ul><li>Home</li><li>About us</li><li>Services</li><li>Products</li><li>Contact</li></ul></div>
  <div class="f-col abs" style="left:571px"><h4>PRODUCTS</h4><ul><li>Sed porta</li><li>Suspendisse quam</li><li>Leo molestie</li><li>Sed luctus</li><li>Fermentum</li></ul></div>
  <div class="f-col abs" style="left:750px"><h4>RESOURCES</h4><ul><li>FAQ</li><li>Videos</li><li>News</li><li>Contact Us</li></ul></div>
  <div class="f-col abs social" style="left:915px">
    <h4>GET IN TOUCH</h4>
    <ul><li><span class="dot"></span>Chirpline</li><li><span class="dot"></span>Friendwall</li><li><span class="dot"></span>Worklane</li><li><span class="dot"></span>Snapframe</li></ul>
  </div>
</footer>
<div class="copyright">Copyright © 2019 All right reserved</div>

</body>
</html>
```